Marlowe Group needs a business card

I would like the card to be simple but modern and elegant.
I like black and white.
or black and gold.
we are a private finance lender and also are involved in property and property developments.

please look at the business card photos i provided i would like M.G only one one side and all the other details on the other side use fonts that tie in with my theme.

Industry/Entity Type

Finance

Contact Information for Business Card

Marlowe Group (M.G) Daniel Marlowe M: 0413586207 E: danmarl@inboxmail.test

Font styles to use
Other font styles liked:
• Use fonts that would reflect our business

Colors
000000
ffffff

Requirements
Must have
• one side of details
• other side has either M.G or Marlowe Group like in the photos provided

```html
<!DOCTYPE html>
<html lang="en">
<head>
<meta charset="utf-8">
<title>Marlowe Group — Business Card</title>
<link href="https://fonts.googleapis.com/css2?family=Ubuntu:wght@300;400;500;700&display=swap" rel="stylesheet">
<style>
  :root {
    --ink: #000000;
    --paper: #ffffff;
    --backdrop: #e8e6e2;
    --rule: #1a1a1a;
    --rule-light: #d9d9d9;
  }
  * { box-sizing: border-box; margin: 0; padding: 0; }
  html, body {
    width: 1200px; height: 789px; overflow: hidden;
    background: var(--backdrop);
    font-family: "Ubuntu", sans-serif;
  }
  .sheet {
    width: 1200px; height: 789px;
    display: flex; align-items: center; justify-content: center; gap: 40px;
  }
  .card {
    position: relative;
    width: 540px; height: 309px;
    overflow: hidden;
    box-shadow: 0 6px 18px rgba(0,0,0,.18);
  }
  /* Back: monogram */
  .card--back { background: var(--ink); }
  .monogram {
    position: absolute; left: 0; right: 0; top: 92px;
    display: flex; align-items: center; justify-content: center; gap: 18px;
  }
  .monogram__rule { width: 120px; height: 1px; background: var(--rule-light); margin-top: 22px; }
  .monogram__letters {
    color: var(--paper); font-weight: 400; font-size: 68px;
    letter-spacing: 10px; line-height: 1;
  }
  /* Front: details */
  .card--front { background: var(--paper); border: 1px solid #cfcfcf; }
  .brand {
    position: absolute; left: 56px; top: 56px; right: 26px;
    display: flex; align-items: flex-end; gap: 8px;
  }
  .brand__name {
    color: var(--ink); font-weight: 700; font-size: 38px;
    letter-spacing: -1px; line-height: 1; white-space: nowrap;
  }
  .brand__suffix {
    color: var(--ink); font-weight: 500; font-size: 20px;
    line-height: 1; white-space: nowrap; margin-bottom: 12px;
  }
  .brand__rule { flex: 1; height: 1px; background: var(--rule); margin-bottom: 14px; }
  .band { position: absolute; left: 0; top: 0; width: 540px; height: 309px; }
  .holder {
    position: absolute; left: 64px; bottom: 14px;
    color: var(--paper); font-weight: 500; font-size: 21px; letter-spacing: .3px;
    white-space: nowrap;
  }
  .contact {
    position: absolute; left: 368px; top: 232px;
    list-style: none; color: var(--paper); font-weight: 300; font-size: 12px;
  }
  .contact__item { display: flex; align-items: center; gap: 7px; height: 22px; white-space: nowrap; }
  .contact__icon { width: 14px; height: 14px; flex: none; }
</style>
</head>
<body>
<main class="sheet">
  <section class="card card--back" aria-label="Card back">
    <div class="monogram">
      <span class="monogram__rule"></span>
      <span class="monogram__letters">MG</span>
      <span class="monogram__rule"></span>
    </div>
  </section>

  <section class="card card--front" aria-label="Card front">
    <div class="brand">
      <span class="brand__name">Marlowe</span>
      <span class="brand__suffix">Group</span>
      <span class="brand__rule"></span>
    </div>

    <svg class="band" viewBox="0 0 540 309" aria-hidden="true">
      <polygon points="0,254 302,254 352,309 0,309" fill="#000"/>
      <polygon points="326,222 540,222 540,309 384,309" fill="#000"/>
    </svg>

    <p class="holder">Daniel Marlowe</p>

    <ul class="contact">
      <li class="contact__item">
        <svg class="contact__icon" viewBox="0 0 14 14" aria-hidden="true">
          <rect x="0" y="0" width="14" height="14" rx="3" fill="#fff"/>
          <rect x="4.5" y="2.5" width="5" height="9" rx="1" fill="#000"/>
          <rect x="5.5" y="3.8" width="3" height="5" fill="#fff"/>
        </svg>
        <span>0413586207</span>
      </li>
      <li class="contact__item">
        <svg class="contact__icon" viewBox="0 0 14 14" aria-hidden="true">
          <rect x="0" y="0" width="14" height="14" rx="3" fill="#fff"/>
          <rect x="2.5" y="4" width="9" height="6.5" fill="none" stroke="#000" stroke-width="1"/>
          <polyline points="2.5,4 7,8 11.5,4" fill="none" stroke="#000" stroke-width="1"/>
        </svg>
        <span>danmarl@inboxmail.test</span>
      </li>
    </ul>
  </section>
</main>
</body>
</html>
```